Custom unique Stationary design for Logistics company

We need a custom, unique , elegant and luxurious full stationary design using our new logo, following these guidelines:
1- Business card: double sided, both sides uses the navy blue as the background main color (same as the code of the navy blue used in our logo).
2- envelope and folder: also use the same navy blue as the main background color.
3- book cover( notepad cover) : same thing with the navy blue
4- letterhead: feel free to use the combination of the colors in our logo.
5- rest of the items are up to your creativity

Target Market(s)

corporates and other businesses

Industry/Entity Type

Logistics and heavy machines contractors

Requirements
Must have
• Letterhead, business card, envelope, notepad cover, paper, file
Nice to have
• navy blue to be main background color for business card, envelope, notepad cover

```html
<!DOCTYPE html>
<html lang="en">
<head>
<meta charset="utf-8">
<title>Kestrel Haulage Letterhead</title>
<link href="https://fonts.googleapis.com/css2?family=Open+Sans:wght@600;700&display=swap" rel="stylesheet">
<style>
  :root {
    --navy: #0f4a72;
    --navy-deep: #0b3a5c;
    --orange: #ef6a3c;
    --paper: #ffffff;
    --backdrop: #a9cdee;
    --ink: #5a5f66;
  }
  html, body {
    margin: 0;
    width: 1200px;
    height: 784px;
    overflow: hidden;
    background: var(--backdrop);
    font-family: "Open Sans", Arial, sans-serif;
  }
  .letterhead {
    position: absolute;
    left: 340px;
    top: 22px;
    width: 520px;
    height: 740px;
    background: var(--paper);
    box-shadow: 0 6px 24px rgba(20, 60, 110, 0.18);
    overflow: hidden;
  }
  .header-accent {
    position: absolute;
    left: 0;
    top: 30px;
    width: 44px;
    height: 7px;
    background: var(--orange);
  }
  .brand {
    position: absolute;
    left: 54px;
    top: 18px;
    display: flex;
    align-items: center;
    gap: 8px;
    font-weight: 700;
    font-size: 22px;
    line-height: 30px;
    color: var(--navy);
    letter-spacing: 0.5px;
    white-space: nowrap;
  }
  .brand-dot {
    width: 12px;
    height: 12px;
    border-radius: 50%;
    background: var(--orange);
  }
  .header-rule {
    position: absolute;
    left: 282px;
    right: 0;
    top: 54px;
    height: 7px;
    background: var(--navy);
  }
  .footer {
    position: absolute;
    left: 0;
    right: 0;
    bottom: 0;
    height: 60px;
  }
  .footer-stripes {
    position: absolute;
    left: 0;
    right: 0;
    top: 0;
    height: 3px;
  }
  .contact-line {
    position: absolute;
    left: 10px;
    top: 8px;
    display: flex;
    gap: 10px;
    align-items: center;
    font-size: 9.5px;
    font-weight: 600;
    color: var(--ink);
    white-space: nowrap;
  }
  .contact-item { display: flex; align-items: center; gap: 4px; }
  .contact-icon { width: 10px; height: 10px; flex: none; }
  .footer-band {
    position: absolute;
    left: 0;
    right: 0;
    bottom: 0;
    height: 30px;
  }
  .web-address {
    position: absolute;
    right: 18px;
    bottom: 7px;
    font-size: 13px;
    font-weight: 700;
    color: #ffffff;
    white-space: nowrap;
  }
</style>
</head>
<body>
  <main class="letterhead">
    <div class="header-accent"></div>
    <div class="brand"><span class="brand-dot"></span>Kestrel Haulage</div>
    <div class="header-rule"></div>

    <footer class="footer">
      <svg class="footer-stripes" viewBox="0 0 520 3" preserveAspectRatio="none">
        <rect x="0" y="0" width="520" height="3" fill="var(--orange)"/>
      </svg>
      <div class="contact-line">
        <span class="contact-item">
          <svg class="contact-icon" viewBox="0 0 10 10"><circle cx="5" cy="5" r="5" fill="var(--navy)"/><circle cx="5" cy="4.2" r="1.6" fill="#fff"/><path d="M5 8.2 L3.4 5 H6.6 Z" fill="#fff"/></svg>
          48 Harbor Ave, Brookfield, NJ 00000, United States
        </span>
        <span class="contact-item">
          <svg class="contact-icon" viewBox="0 0 10 10"><circle cx="5" cy="5" r="5" fill="var(--navy)"/><path d="M3.3 2.6 L4.4 2.4 L4.9 3.8 L4.2 4.3 Q4.7 5.4 5.7 5.8 L6.2 5.1 L7.6 5.6 L7.4 6.7 Q5.6 7.4 4 5.8 Q2.6 4.3 3.3 2.6 Z" fill="#fff"/></svg>
          +10000000021
        </span>
        <span class="contact-item">
          <svg class="contact-icon" viewBox="0 0 10 10"><circle cx="5" cy="5" r="5" fill="var(--navy)"/><rect x="2.6" y="3.4" width="4.8" height="3.4" fill="#fff"/><path d="M2.6 3.4 L5 5.2 L7.4 3.4" stroke="var(--navy)" stroke-width="0.6" fill="none"/></svg>
          contact@kestrelhaulage.com
        </span>
      </div>
      <svg class="footer-band" viewBox="0 0 520 30" preserveAspectRatio="none">
        <rect x="0" y="18" width="330" height="4" fill="var(--navy)"/>
        <rect x="0" y="24" width="330" height="6" fill="var(--orange)"/>
        <path d="M340 0 H520 V30 H330 Z" fill="var(--navy)"/>
      </svg>
      <div class="web-address">www.kestrelhaulage.com</div>
    </footer>
  </main>
</body>
</html>
```